International professional tennis coach needs a book cover design

This is my 2nd published book, the first one was a #1 on the best seller. I'm looking for a world class book cover design for this new book. The name of my first book was 5 Baseline Habits to Unlock Your Flow Rhythm, located on Bookvale.com

The title of the new book:

Title: The Craft of Rally Mastery
Subtitle: Developing a Strategic Advantage through Competitive Intelligence

I'm uploading our new CRAFT OF RALLY logo that I'd like for you to use as the centerpiece of the book design along with a 21st century design feel that incorporates what the book topic is below::

--> This book is about building competitive intelligence by using tennis data analytics to develop and expand a player's strategic advantage for match play. <--

The colors we would like to use are Blue, Yellow, and Green. These shades of these colors should be bold! (You will see the bold color examples of blues, yellows, and greens that I'm talking about in the logos that are attached here, especially the colors for my Racket GridDrill App logo.

I will upload the Racket GridDrill logo which should go somewhere on the back cover design (small size maybe in the bottom corner).

This book is revolutionary to the standard way of teaching tennis, it is based on a decade of recording and gathering tennis data analytics and then we created on-court practice games to develop better decision making in players for the competitive edge.

My websites are www.elevatedrillzone.com and www.craftofrallymastery.com

```html
<!DOCTYPE html>
<html lang="en">
<head>
<meta charset="utf-8">
<title>The Craft of Rally Mastery — Book Cover</title>
<link href="https://fonts.googleapis.com/css2?family=Archivo+Black&family=Montserrat:wght@500&family=Oswald:wght@300;400;500;600&display=swap" rel="stylesheet">
<style>
  :root {
    --stage: #7aafdc;
    --paper: #f9f4ef;
    --ink: #3d3b39;
    --ink-soft: #3a3a3a;
    --blue: #1a7fc4;
    --blue-line: #1d86d0;
    --yellow: #f6c623;
    --green: #8cc63f;
    --green-pale: #d8e8a4;
  }
  * { margin: 0; padding: 0; box-sizing: border-box; }
  html, body { width: 1200px; height: 1000px; overflow: hidden; }
  body { background: var(--stage); position: relative; font-family: "Oswald", sans-serif; }

  .cover {
    position: absolute; top: 147px; width: 500px; height: 705px;
    background: var(--paper); overflow: hidden;
  }
  .cover--back { left: 60px; }
  .cover--front { left: 640px; }

  /* Back cover */
  .back-tagline {
    position: absolute; left: 36px; top: 28px; width: 460px;
    font-weight: 500; font-size: 15px; line-height: 22px; letter-spacing: -0.2px;
    color: var(--blue); text-transform: uppercase;
  }
  .back-rule { position: absolute; left: 0; top: 73px; width: 500px; height: 3px; background: var(--green); }
  .back-blurb {
    position: absolute; left: 35px; top: 84px; width: 385px;
    font-weight: 300; font-size: 10.6px; line-height: 13.9px; color: var(--ink-soft);
  }
  .back-blurb p { margin-bottom: 7px; }
  .back-blurb p.gap { margin-top: 11px; }
  .bio { position: absolute; left: 35px; width: 440px; }
  .bio--first { top: 341px; }
  .bio--second { top: 496px; }
  .bio-photo { position: absolute; left: 0; top: 0; width: 98px; height: 117px; }
  .bio-text {
    position: absolute; left: 107px; top: -2px; width: 320px;
    font-weight: 300; font-size: 10.6px; line-height: 14.7px; color: var(--ink-soft);
  }
  .bio-name { font-family: "Montserrat", sans-serif; font-weight: 500; color: var(--blue); font-size: 10px; }
  .app-mark {
    position: absolute; left: 28px; top: 630px; width: 120px; text-align: center;
  }
  .app-mark-dot { display: block; width: 22px; height: 22px; border-radius: 50%; background: var(--blue); margin: 0 auto 4px; }
  .app-mark-name { font-weight: 500; font-size: 9px; color: var(--blue); text-transform: uppercase; letter-spacing: 0.4px; }
  .back-sites {
    position: absolute; left: 18px; top: 678px; width: 160px; text-align: center;
    font-family: "Montserrat", sans-serif; font-weight: 500; font-size: 7.8px; line-height: 11px; color: var(--ink-soft);
  }

  /* Front cover */
  .front-art { position: absolute; left: 0; top: 0; width: 500px; height: 705px; }
  .front-title {
    position: absolute; left: 48px; top: 144px;
    font-family: "Archivo Black", sans-serif; font-size: 47px; line-height: 58px;
    color: var(--ink); text-transform: uppercase; letter-spacing: -0.5px;
  }
  .front-rule {
    position: absolute; left: 49px; top: 321px; width: 330px; height: 3px;
    background: linear-gradient(90deg, var(--yellow), var(--green));
  }
  .front-subtitle {
    position: absolute; left: 49px; top: 338px;
    font-weight: 600; font-size: 27px; line-height: 35px; letter-spacing: 0.6px;
    color: var(--blue); text-transform: uppercase;
  }
  .front-authors {
    position: absolute; left: 150px; top: 594px; width: 205px; text-align: center;
    font-family: "Montserrat", sans-serif; font-weight: 500; font-size: 16px; line-height: 21px;
    color: var(--ink); text-transform: uppercase;
  }
</style>
</head>
<body>

<section class="cover cover--back">
  <h2 class="back-tagline">A practical guide on how to win more matches by becoming a more efficient and effective competitor.</h2>
  <div class="back-rule"></div>
  <div class="back-blurb">
    <p>As a tennis player you have the ability to play better matches and win more of them. The Craft of Rally Mastery gives you a system to improve. We start with the individual game of the set itself. Our system examines your physical and mental progression, enabling you to upgrade your movement and performance from shot to shot and point to point. Our system seamlessly integrates the technical (physical) aspects with the tactical (mental/emotional) components, providing a comprehensive approach to elevate this performance.</p>
    <p>We aim to give you much more than how to hit great shots. Irrespective of your current skill level, we will provide you with a detailed strategic and tactical plan to enhance your performance, leading to improved results and increased success in your matches.</p>
    <p>The Craft of Rally Mastery emphasizes the importance of shifting focus from oneself to the opponent, encouraging players to analyze and understand their adversaries. By bringing the opponent back to the forefront of their thinking, the player creates the best possible context in which to improve as a competitor.</p>
    <p class="gap">In this book, we present a groundbreaking approach to tennis data analytics that seamlessly integrates match performance with practice sessions, and vice versa.</p>
  </div>

  <div class="bio bio--first">
    <svg class="bio-photo" viewBox="0 0 98 117" role="img" aria-label="Portrait photo of author Corwin Haldane on a tennis court">
      <defs><linearGradient id="photoA" x1="0" y1="0" x2="0" y2="1"><stop offset="0" stop-color="#6f6a5e"/><stop offset="1" stop-color="#3b3d44"/></linearGradient></defs>
      <rect width="98" height="117" fill="url(#photoA)"/>
    </svg>
    <p class="bio-text"><span class="bio-name">Corwin Haldane</span> is regarded as one of the leading strategy and tactical coaches in the world today. He is the Creator of Racket GridDrill, the world's first Tennis Tracking App that maps and charts match play based on the rally length of a point. Corwin is a Best Selling Author of the book "5 Baseline Habits to Unlock Your Flow Rhythm" and the Co-Founder of The Craft of Rally Mastery promoting coach, player, and parent development. He is often sought after by coaches around the world to design the practice court in a way that revolutionizes a player's mindset to successfully negotiate the pressures of competitive match play.</p>
  </div>

  <div class="bio bio--second">
    <svg class="bio-photo" viewBox="0 0 98 117" role="img" aria-label="Portrait photo of author Mylo Brennick outdoors">
      <defs><linearGradient id="photoB" x1="0" y1="0" x2="0" y2="1"><stop offset="0" stop-color="#8fb4c9"/><stop offset="1" stop-color="#3f4b5e"/></linearGradient></defs>
      <rect width="98" height="117" fill="url(#photoB)"/>
    </svg>
    <p class="bio-text"><span class="bio-name">Mylo Brennick</span> is a writer and tennis coach. He is a Co-Founder at The Craft of Rally Mastery and has been working to create a theoretical framework for tennis players of all levels to improve. Mylo studies the forces that act on the player during a tennis match (both internal and external) and works with players to meet the challenge these forces represent. He runs online and on court programs designed specifically to improve a player's Competitive Intelligence.</p>
  </div>

  <div class="app-mark">
    <span class="app-mark-dot"></span>
    <span class="app-mark-name">Racket GridDrill</span>
  </div>
  <p class="back-sites">www.elevatedrillzone.com<br>www.craftofrallymastery.com</p>
</section>

<section class="cover cover--front">
  <svg class="front-art" viewBox="0 0 500 705">
    <g class="stripes">
      <polygon points="0,0 200,0 0,58" fill="var(--green-pale)"/>
      <polygon points="0,66 225,0 265,0 0,80" fill="var(--green-pale)" opacity="0.7"/>
      <polygon points="500,605 500,705 160,705" fill="var(--green-pale)"/>
      <polygon points="500,585 500,596 125,705 95,705" fill="var(--green-pale)" opacity="0.7"/>
    </g>
    <g class="connectors" stroke="var(--blue-line)" stroke-width="3">
      <line x1="439" y1="148" x2="428" y2="184"/>
      <line x1="430" y1="304" x2="452" y2="308"/>
      <line x1="452" y1="438" x2="426" y2="443"/>
    </g>
    <g class="medal-circle">
      <circle cx="439" cy="83" r="62" fill="none" stroke="var(--yellow)" stroke-width="7"/>
      <circle cx="439" cy="83" r="53" fill="#2b3442" role="img" aria-label="Photo of a raised hand holding a first place medal"/>
    </g>
    <g class="analytics-circle">
      <circle cx="423" cy="244" r="56" fill="none" stroke="var(--yellow)" stroke-width="7"/>
      <circle cx="423" cy="244" r="47" fill="#eef3dd" role="img" aria-label="Green line-art illustration of a networked brain"/>
    </g>
    <g class="ball-circle">
      <circle cx="466" cy="372" r="62" fill="none" stroke="var(--yellow)" stroke-width="7"/>
      <circle cx="466" cy="372" r="53" fill="#2a8fcf" role="img" aria-label="Photo of a tennis ball on a blue court"/>
    </g>
    <g class="chart-circle">
      <circle cx="410" cy="497" r="52" fill="none" stroke="var(--yellow)" stroke-width="7"/>
      <circle cx="410" cy="497" r="44" fill="#2a86cc" role="img" aria-label="Blue and yellow data chart illustration"/>
    </g>
  </svg>
  <h1 class="front-title">The Craft<br>of Rally<br>Mastery</h1>
  <div class="front-rule"></div>
  <p class="front-subtitle">Developing a Strategic<br>Advantage through<br>Competitive Intelligence</p>
  <p class="front-authors">Corwin Haldane<br>&amp; Mylo Brennick</p>
</section>

</body>
</html>
```